Shopify Web-Page "Tiny-ThreadDays

We are building a new business in Switzerland offering premium sewing holiday camps for kids aged 9–14. In enclosed brief outlines our requirements for a complete Shopify homepage design and a multilingual logo creation.
Domains: tiny-threaddays.ch ; tiny-giornifilo.ch ; tiny-fadentage.ch

Project Overview
We are looking for:
1. A modern, fully designed Shopify homepage in English using standard Shopify content blocks (no custom coding), which we can later update ourselves. Supporting Multilanguage (EN, German, Italian).

2. A logo design that includes the brand identity and communicates our multilingual, creative, and child-focused positioning.

All details in enclosed

```html
<!DOCTYPE html>
<html lang="en">
<head>
<meta charset="utf-8">
<title>Tiny-ThreadDays – Sewing Holiday Camps</title>
<link href="https://fonts.googleapis.com/css2?family=Fredoka:wght@500;600;700&family=Poppins:wght@400;500;600&display=swap" rel="stylesheet">
<style>
:root{
  --purple:#8a68a6;--pink:#e2577a;--blue:#2b9dd0;--yellow:#efbb22;--teal:#2f8f86;
  --ink:#1f2430;--muted:#5b6170;--sky:#e9f5fb;--navy:#1c2a3e;--line:#e6e8ee;
}
*{box-sizing:border-box;margin:0;padding:0}
html,body{width:1200px;height:4906px;overflow:hidden;background:#fff}
body{font-family:"Poppins",sans-serif;color:var(--ink);font-size:12px;position:relative}
.abs{position:absolute}
h1,h2,h3,.display{font-family:"Fredoka",sans-serif}
.eyebrow{font-family:"Poppins",sans-serif;font-weight:600;font-size:14px;color:var(--blue);letter-spacing:.3px;text-transform:uppercase;text-align:center}
.title{font-family:"Poppins",sans-serif;font-weight:500;font-size:25px;text-transform:uppercase;text-align:center;margin-top:10px;letter-spacing:.2px}
.title em{font-style:normal;color:var(--pink);border-bottom:3px solid var(--pink);padding-bottom:1px}
.btn{display:inline-flex;align-items:center;gap:10px;border-radius:30px;font-size:13px;padding:8px 10px 8px 18px;color:#fff}
.btn i{width:24px;height:24px;border-radius:50%;background:#fff;display:inline-flex;align-items:center;justify-content:center}
.brand{font-family:"Fredoka",sans-serif;font-weight:700;color:var(--pink)}
/* nav */
.nav{top:0;left:0;width:1200px;height:78px;display:flex;align-items:center;padding:0 64px;background:#fff;z-index:2}
.nav .brand{font-size:20px;width:160px}
.nav ul{display:flex;gap:28px;list-style:none;font-size:12px;margin-left:12px}
.nav ul li:first-child{font-weight:600}
.nav .lang{margin-left:auto;font-size:12px;display:flex;align-items:center;gap:6px}
.nav .btn{margin-left:30px;background:var(--pink);padding:6px 6px 6px 16px}
/* hero */
.hero{top:78px;left:0;width:1200px;height:542px;background:#f3f2f6}
.hero .photo{left:420px;top:0;width:780px;height:542px;background:linear-gradient(120deg,#f3f2f6 0%,#e9c79a 35%,#d89a4a 60%,#c46a3a 100%)}
.hero h1{left:64px;top:80px;font-size:40px;line-height:55px;font-weight:600;text-transform:uppercase;color:var(--ink)}
.hero h1 span{color:#3a6aa8;font-weight:700}
.hero p{left:64px;top:248px;width:350px;font-size:13px;line-height:23px}
.hero .btn{left:64px;top:354px;background:var(--purple)}
.hero .join{left:64px;top:442px;font-size:13px;display:flex;gap:10px;align-items:center}
/* about */
.about-img{left:140px;top:700px;width:420px;height:420px}
.about{left:600px;top:706px;width:470px}
.about .eyebrow{text-align:left}
.about h2{font-family:"Poppins",sans-serif;font-weight:500;font-size:24px;text-transform:uppercase;margin:8px 0 20px}
.about h2 em{font-style:normal;color:var(--pink);border-bottom:3px solid var(--pink)}
.about p{font-size:12px;line-height:21px;color:var(--muted);margin-bottom:14px}
.team{display:flex;gap:40px;margin-top:22px}
.member{display:flex;gap:14px;align-items:center}
.avatar{width:66px;height:66px;border-radius:50%;background:linear-gradient(135deg,#e9d6cf,#8d6b5c)}
.member b{font-size:16px;font-weight:600;display:block}
.member span{font-size:13px;color:var(--muted)}
/* how */
.how{top:1190px;left:0;width:1200px;height:550px}
.how-head{top:1328px;left:0;width:1200px}
.steps{top:1418px;left:140px;width:920px;display:flex;gap:18px}
.step{flex:1;background:#fff;border-radius:6px;height:212px;padding:16px 14px;position:relative;box-shadow:0 4px 14px rgba(40,60,90,.06)}
.step .num{position:absolute;right:14px;top:8px;font-family:"Fredoka",sans-serif;font-size:44px;font-weight:600;color:#eef0f4}
.step h3{font-family:"Poppins",sans-serif;font-size:14px;font-weight:500;margin:12px 0 6px}
.step p{font-size:12px;line-height:19px;color:var(--muted)}
/* why */
.why-head{top:1836px;left:0;width:1200px}
.circle{left:448px;top:1953px;width:302px;height:302px;border:2px dashed #6b6f7a;border-radius:50%;display:flex;align-items:center;justify-content:center}
.circle .inner{width:200px;height:200px;border-radius:50%;background:#fff;box-shadow:0 6px 24px rgba(0,0,0,.1);display:flex;align-items:center;justify-content:center;text-align:center;font-size:28px;line-height:30px}
.feat{display:flex;align-items:center;gap:18px;font-size:13px;line-height:23px}
.feat .ic{width:72px;height:72px;border-radius:50%;flex:none;display:flex;align-items:center;justify-content:center}
.feat.l{text-align:right}
.divider{top:2348px;left:140px;width:920px;height:1px;background:var(--line)}
/* camps */
.camps-head{top:2418px;left:0;width:1200px}
.cards{top:2510px;left:140px;width:920px;display:flex;gap:34px}
.card{flex:1;border:1px solid var(--line);border-radius:6px;overflow:hidden;height:376px}
.card .ph{height:164px}
.card .bd{padding:16px 16px}
.card h3{font-family:"Poppins",sans-serif;font-size:14px;font-weight:500;margin-bottom:8px}
.card p{font-size:12px;line-height:20px;color:var(--muted);height:82px}
.meta{display:grid;grid-template-columns:1fr 1fr;row-gap:12px;font-size:12px;margin-top:16px;color:var(--muted)}
.meta b{font-weight:600;color:var(--ink);margin-right:14px}
.view{top:2912px;left:518px;background:var(--pink)}
/* cta */
.cta{top:3040px;left:0;width:1200px;height:390px}
.cta-text{top:3148px;left:0;width:1200px;text-align:center;color:#fff}
.cta-text h2{font-size:38px;font-weight:700;letter-spacing:.5px}
.cta-text p{font-size:14px;line-height:25px;width:620px;margin:14px auto 22px}
.cta-text .btn{background:#fff;color:var(--blue)}
/* faq */
.faq-head{top:3524px;left:0;width:1200px}
.faq{top:3612px;left:177px;width:846px}
.q{height:58px;border-radius:4px;box-shadow:0 3px 12px rgba(30,40,60,.08);border-left:3px solid var(--pink);display:flex;align-items:center;justify-content:space-between;padding:0 20px;font-size:14px;font-weight:500;margin-bottom:23px}
.q.open{height:114px;border:1.5px solid var(--pink);flex-direction:column;align-items:stretch;justify-content:center}
.q.open .row{display:flex;justify-content:space-between}
.q.open p{font-size:12px;font-weight:400;color:var(--muted);line-height:21px;margin-top:10px}
/* footer */
.foot{top:4540px;left:0;width:1200px;height:366px}
.foot-in{top:4640px;left:144px;width:920px;display:flex;color:#fff}
.foot-in h4{font-family:"Poppins",sans-serif;font-weight:500;font-size:15px;color:var(--yellow);margin-bottom:20px}
.foot-in ul{list-style:none;font-size:12px;line-height:29px}
.foot-in .contact li{display:flex;gap:14px;align-items:center;margin-bottom:20px;font-size:12px;line-height:20px}
.contact .ci{width:30px;height:30px;border-radius:50%;background:#2e3d52;flex:none;display:flex;align-items:center;justify-content:center}
.social{width:20px;height:20px;border:1px solid #fff;border-radius:50%}
.mail{width:246px;height:34px;border-radius:20px;background:#fff;display:flex;align-items:center;justify-content:space-between;padding:0 4px 0 14px;color:#999;font-size:11px;margin-top:14px}
.copy{top:4872px;left:0;width:1200px;text-align:center;color:#d7dbe3;font-size:11px}
</style>
</head>
<body>

<header class="nav abs">
  <div class="brand">Tiny-ThreadDays</div>
  <ul><li>Home</li><li>About Us</li><li>Camps</li><li>How It Works</li><li>FAQs</li><li>Contact</li></ul>
  <div class="lang">
    <svg width="14" height="14" viewBox="0 0 24 24" fill="none" stroke="#333" stroke-width="2"><circle cx="12" cy="12" r="10"/><path d="M2 12h20M12 2c3 3 3 17 0 20M12 2c-3 3-3 17 0 20"/></svg>
    English &nbsp;
    <svg width="12" height="12" viewBox="0 0 24 24" fill="none" stroke="#333" stroke-width="2"><path d="M6 9l6 6 6-6"/></svg>
  </div>
  <span class="btn">Contact Us <i><svg width="12" height="12" viewBox="0 0 24 24" fill="none" stroke="#e2577a" stroke-width="3"><path d="M7 17L17 7M9 7h8v8"/></svg></i></span>
</header>

<section class="hero abs">
  <div class="photo abs" role="img" aria-label="Group of smiling children holding colourful sewn fabrics around a wooden table"></div>
  <svg class="abs" style="left:0;bottom:-1px" width="1200" height="70" viewBox="0 0 1200 70" preserveAspectRatio="none"><path d="M0 40 C200 75 350 10 600 30 S1000 70 1200 30 V70 H0Z" fill="#fff"/></svg>
  <h1 class="abs"><span>Premium Sewing<br>Holiday</span> Camps<br>for Kids 9-14</h1>
  <p class="abs">Creative fun in Zurich – Multilingual and Inspiring! Learn sewing, build confidence, and create unique fashion pieces in our small-group camps.</p>
  <span class="btn abs">View Upcoming Camps <i><svg width="12" height="12" viewBox="0 0 24 24" fill="none" stroke="#8a68a6" stroke-width="3"><path d="M7 17L17 7M9 7h8v8"/></svg></i></span>
  <div class="join abs"><svg width="20" height="20" viewBox="0 0 24 24" fill="none" stroke="#333" stroke-width="1.6"><circle cx="12" cy="12" r="10"/><path d="M8 14c1.5 2 6.5 2 8 0"/><circle cx="9" cy="10" r="1"/><circle cx="15" cy="10" r="1"/></svg> Join 200+ happy campers!</div>
</section>

<svg class="about-img abs" viewBox="0 0 420 420" role="img" aria-label="Collage of children sewing and cutting fabric">
  <path d="M210 0 A210 210 0 0 0 50 80 L50 180 L205 180 L205 0Z" fill="#c9b49a"/>
  <path d="M215 20 A190 190 0 0 1 390 180 L215 180Z" fill="#efbb22"/>
  <path d="M215 60 A130 130 0 0 1 340 180 L215 180Z" fill="#2f8f86"/>
  <path d="M0 190 L205 190 L205 420 A210 210 0 0 1 0 190Z" fill="#d9cfc8"/>
  <path d="M215 190 L420 190 A210 210 0 0 1 215 400Z" fill="#b5b0b8"/>
  <circle cx="210" cy="185" r="30" fill="#fff"/>
  <circle cx="210" cy="185" r="22" fill="#fbe3ea"/>
  <path d="M210 195 l-9-9a5 5 0 0 1 9-6 5 5 0 0 1 9 6z" fill="#e2577a"/>
</svg>

<section class="about abs">
  <div class="eyebrow">About our camps</div>
  <h2>Learning with fun <em>&amp; Structure</em></h2>
  <p>At Tiny-ThreadDays, we believe in nurturing creativity while having fun. Our experienced instructors create a safe, inspiring environment where children can explore their creative potential.</p>
  <p>With over 10 years of experience in teaching children sewing, tailoring, and design, Marta and Lena guide young talents through a creative week of vacation – with real results: self-sewn pieces, new friends, and lots of pride.</p>
  <p>At the last day, the children show off their success, their own sewn unique pieces, in a sympathetic fashion show.</p>
  <div class="team">
    <div class="member"><div class="avatar" role="img" aria-label="Portrait of Marta"></div><div><b>Marta</b><span>Sewing Expert</span></div></div>
    <div class="member"><div class="avatar" role="img" aria-label="Portrait of Lena"></div><div><b>Lena</b><span>Design Specialist</span></div></div>
  </div>
</section>

<svg class="how abs" viewBox="0 0 1200 550" preserveAspectRatio="none"><path d="M0 30 C250 -10 450 60 700 30 S1050 0 1200 25 V520 C950 560 700 490 450 520 S150 560 0 520Z" fill="#e9f5fb"/></svg>
<div class="how-head abs"><div class="eyebrow">How our camps work</div><div class="title">Creative holiday camps for young <em>Sewing Champs!</em></div></div>
<div class="steps abs">
  <div class="step"><span class="num">01</span><svg width="40" height="36" viewBox="0 0 24 24" fill="none" stroke="#e2577a" stroke-width="1.4"><path d="M4 20L18 6M14 4l6 6M6 14l4 4"/></svg><h3>Project Selection</h3><p>Your child chooses their own model based on previously produced clothing items and sewing patterns.</p></div>
  <div class="step"><span class="num">02</span><svg width="40" height="36" viewBox="0 0 24 24" fill="none" stroke="#e2577a" stroke-width="1.4"><rect x="4" y="6" width="16" height="12" rx="2"/><path d="M4 10h16M4 14h16"/></svg><h3>Fabric selection</h3><p>High-quality fabrics are available.</p></div>
  <div class="step"><span class="num">03</span><svg width="40" height="36" viewBox="0 0 24 24" fill="none" stroke="#e2577a" stroke-width="1.4"><path d="M3 18h18M5 18V8h12v4h-2v6M9 8v-2h6"/></svg><h3>Sewing machine</h3><p>Learn how to use a sewing machine</p></div>
  <div class="step"><span class="num">04</span><svg width="40" height="36" viewBox="0 0 24 24" fill="none" stroke="#e2577a" stroke-width="1.4"><path d="M6 4h12l-4 8v8h-4v-8z"/></svg><h3>Sewing &amp; refining</h3><p>Step by step to the goal with professional guidance</p></div>
  <div class="step"><span class="num">05</span><svg width="40" height="36" viewBox="0 0 24 24" fill="none" stroke="#e2577a" stroke-width="1.4"><path d="M8 4l4 3 4-3 4 4-3 3v9H7v-9L4 8z"/></svg><h3>Showtime!</h3><p>Fashion show or photo shoot at the end of the week</p></div>
</div>

<div class="why-head abs"><div class="eyebrow">Why parents choose us</div><div class="title">Why families love Tiny-ThreadDays sewing <em>Camps</em></div></div>
<div class="circle abs"><div class="inner"><span class="brand">Tiny-<br>Thread<br>Days</span></div></div>
<div class="feat l abs" style="top:1944px;right:788px">Small groups &amp;<br>personalized attention<span class="ic" style="background:var(--yellow)"><svg width="30" height="30" viewBox="0 0 24 24" fill="none" stroke="#fff" stroke-width="2"><path d="M5 5l6 6M11 6v5H6M19 19l-6-6M13 18v-5h5"/></svg></span></div>
<div class="feat l abs" style="top:2068px;right:812px">Multilingual supervision<br>(DE / EN / IT)<span class="ic" style="background:var(--blue)"><svg width="30" height="30" viewBox="0 0 24 24" fill="none" stroke="#fff" stroke-width="2"><path d="M4 5h9M8 3v2M6 5c1 4 4 7 7 8M11 5c-1 4-4 7-7 8M13 21l4-9 4 9M14.5 18h5"/></svg></span></div>
<div class="feat l abs" style="top:2192px;right:788px">Pick-up Service from the<br>Main-Station<span class="ic" style="background:var(--pink)"><svg width="28" height="28" viewBox="0 0 24 24" fill="#fff"><path d="M12 2a7 7 0 0 0-7 7c0 5 7 13 7 13s7-8 7-13a7 7 0 0 0-7-7zm0 9a2.5 2.5 0 1 1 0-5 2.5 2.5 0 0 1 0 5z"/></svg></span></div>
<div class="feat abs" style="top:1944px;left:772px"><span class="ic" style="background:var(--blue)"><svg width="30" height="30" viewBox="0 0 24 24" fill="none" stroke="#fff" stroke-width="2"><path d="M12 3l2.7 5.6 6.1.9-4.4 4.3 1 6.1L12 17l-5.4 2.9 1-6.1-4.4-4.3 6.1-.9z"/></svg></span>Encouragement of creativity,<br>self-confidence, and fine<br>motor skills</div>
<div class="feat abs" style="top:2068px;left:800px"><span class="ic" style="background:var(--pink)"><svg width="28" height="28" viewBox="0 0 24 24" fill="none" stroke="#fff" stroke-width="2"><path d="M12 3l8 3v6c0 5-4 8-8 9-4-1-8-4-8-9V6z"/><path d="M9 12l2 2 4-4"/></svg></span>Safe, loving environment in<br>Zurich, various places easy<br>to reach</div>
<div class="feat abs" style="top:2192px;left:772px"><span class="ic" style="background:var(--yellow)"><svg width="30" height="30" viewBox="0 0 24 24" fill="none" stroke="#fff" stroke-width="1.6"><rect x="4" y="4" width="16" height="16" rx="2"/><path d="M4 9h16M4 14h16M9 4v16M14 4v16"/></svg></span>High-quality fabrics &amp; top-<br>quality sewing machines<br>(Stitchwell)</div>

<div class="divider abs"></div>

<div class="camps-head abs"><div class="eyebrow">Our upcoming camps</div><div class="title">Multilingual creativity, made just <em>For Kids</em></div></div>
<div class="cards abs">
  <div class="card"><div class="ph" role="img" aria-label="Instructor helping a child at a sewing table" style="background:linear-gradient(135deg,#c9d7d9,#8a7a6c)"></div><div class="bd"><h3>Spring Sewing Camp</h3><p>Join us for a creative week during spring break! Children will learn sewing basics and create their own spring-themed projects.</p><div class="meta"><span><b>Age:</b>09 to 14</span><span><b>Total:</b>200 Kids</span><span><b>Date:</b>21 Oct,2025</span><span><b>Duration:</b>06 Days</span></div></div></div>
  <div class="card"><div class="ph" role="img" aria-label="Children running across a sunny park" style="background:linear-gradient(135deg,#8fb464,#4e7a3a)"></div><div class="bd"><h3>Summer Fashion Camp</h3><p>Our popular summer program where kids design and create their own summer wardrobe items in a fun, supportive environment.</p><div class="meta"><span><b>Age:</b>09 to 14</span><span><b>Total:</b>200 Kids</span><span><b>Date:</b>07 Jul,2025</span><span><b>Duration:</b>06 Days</span></div></div></div>
  <div class="card"><div class="ph" role="img" aria-label="Children sewing at machines in a bright workshop" style="background:linear-gradient(135deg,#e8ded4,#a58e9a)"></div><div class="bd"><h3>Autumn Creative Camp</h3><p>Get ready for cooler weather by creating cozy autumn accessories and clothing items in this creative camp Autumn Creative Camp.</p><div class="meta"><span><b>Age:</b>09 to 14</span><span><b>Total:</b>200 Kids</span><span><b>Date:</b>21 Oct,2025</span><span><b>Duration:</b>06 Days</span></div></div></div>
</div>
<span class="btn view abs">View All Camps <i><svg width="12" height="12" viewBox="0 0 24 24" fill="none" stroke="#e2577a" stroke-width="3"><path d="M7 17L17 7M9 7h8v8"/></svg></i></span>

<svg class="cta abs" viewBox="0 0 1200 390" preserveAspectRatio="none"><path d="M0 30 C250 -10 500 60 750 25 S1050 10 1200 30 V370 C950 400 700 340 450 370 S150 395 0 365Z" fill="#8a68a6"/></svg>
<div class="cta-text abs">
  <h2>READY FOR A CREATIVE ADVENTURE?</h2>
  <p>Spaces are limited to 8 children per camp to ensure personalized attention. Book now to secure your child's spot!</p>
  <span class="btn">View All Camps <i style="background:var(--blue)"><svg width="12" height="12" viewBox="0 0 24 24" fill="none" stroke="#fff" stroke-width="3"><path d="M7 17L17 7M9 7h8v8"/></svg></i></span>
</div>

<div class="faq-head abs"><div class="eyebrow">Frequently asked questions</div><div class="title">Everything you need to know about <em>Our Camps</em></div></div>
<div class="faq abs">
  <div class="q open"><div class="row">Does my child need any prior knowledge?<svg width="16" height="16" viewBox="0 0 24 24" fill="none" stroke="#333" stroke-width="2"><path d="M6 15l6-6 6 6"/></svg></div><p>We welcome children aged 9-14 years. This age range ensures that participants have the fine motor skills needed for sewing while still being excited about creative projects.</p></div>
  <div class="q">How does the pick-up service work?<svg width="16" height="16" viewBox="0 0 24 24" fill="none" stroke="#333" stroke-width="2"><path d="M6 9l6 6 6-6"/></svg></div>
  <div class="q">How many items of clothing are produced?<svg width="16" height="16" viewBox="0 0 24 24" fill="none" stroke="#333" stroke-width="2"><path d="M6 9l6 6 6-6"/></svg></div>
  <div class="q">What should my child bring to camp?<svg width="16" height="16" viewBox="0 0 24 24" fill="none" stroke="#333" stroke-width="2"><path d="M6 9l6 6 6-6"/></svg></div>
  <div class="q">What are the camp hours?<svg width="16" height="16" viewBox="0 0 24 24" fill="none" stroke="#333" stroke-width="2"><path d="M6 9l6 6 6-6"/></svg></div>
  <div class="q">We offer pick-up from Zurich Main Station at times. Parents can arrange this during booking<svg width="16" height="16" viewBox="0 0 24 24" fill="none" stroke="#333" stroke-width="2"><path d="M6 9l6 6 6-6"/></svg></div>
  <div class="q">What is your cancellation policy?<svg width="16" height="16" viewBox="0 0 24 24" fill="none" stroke="#333" stroke-width="2"><path d="M6 9l6 6 6-6"/></svg></div>
  <div class="q">How many items of clothing are produced?<svg width="16" height="16" viewBox="0 0 24 24" fill="none" stroke="#333" stroke-width="2"><path d="M6 9l6 6 6-6"/></svg></div>
  <div class="q">Each child completes their own unique clothing item during the week<svg width="16" height="16" viewBox="0 0 24 24" fill="none" stroke="#333" stroke-width="2"><path d="M6 9l6 6 6-6"/></svg></div>
  <div class="q">What safety measures are in place?<svg width="16" height="16" viewBox="0 0 24 24" fill="none" stroke="#333" stroke-width="2"><path d="M6 9l6 6 6-6"/></svg></div>
</div>

<svg class="foot abs" viewBox="0 0 1200 366" preserveAspectRatio="none"><path d="M0 20 C300 -5 600 45 900 15 S1150 5 1200 20 V366 H0Z" fill="#1c2a3e"/></svg>
<footer class="foot-in abs">
  <div style="width:220px">
    <div class="brand" style="font-size:24px;margin-top:10px">Tiny-ThreadDays</div>
    <div style="font-size:12px;margin-top:74px;display:flex;gap:8px;align-items:center">Follow Us: <span class="social"></span><span class="social"></span><span class="social"></span></div>
  </div>
  <div style="width:150px"><h4>Quick Links</h4><ul><li>Home</li><li>About Us</li><li>Camps</li><li>How It Works</li><li>Contact</li></ul></div>
  <div style="width:296px"><h4>Contact Us</h4><ul class="contact">
    <li><span class="ci"><svg width="14" height="14" viewBox="0 0 24 24" fill="#fff"><path d="M12 2a7 7 0 0 0-7 7c0 5 7 13 7 13s7-8 7-13a7 7 0 0 0-7-7z"/></svg></span>Seefeldweg 14, 8008<br>Zurich, Switzerland</li>
    <li><span class="ci" style="background:var(--blue)"><svg width="14" height="14" viewBox="0 0 24 24" fill="#fff"><path d="M6 3l4 4-2 3c1 2 3 4 6 6l3-2 4 4-3 3C10 21 3 14 3 6z"/></svg></span>Phone: (044)-555 0182</li>
    <li><span class="ci"><svg width="14" height="14" viewBox="0 0 24 24" fill="none" stroke="#fff" stroke-width="2"><rect x="3" y="5" width="18" height="14" rx="2"/><path d="M3 7l9 6 9-6"/></svg></span>info@tiny-threaddays.ch</li>
  </ul></div>
  <div style="width:254px"><h4>Subscribe to newsletter</h4><p style="font-size:12px;line-height:22px">latest updates, exclusive content, and special offers? Subscribe to our newsletter!</p>
    <div class="mail">Your Email<span style="width:28px;height:28px;border-radius:50%;background:var(--blue);display:flex;align-items:center;justify-content:center"><svg width="12" height="12" viewBox="0 0 24 24" fill="none" stroke="#fff" stroke-width="3"><path d="M5 12h14M13 6l6 6-6 6"/></svg></span></div></div>
</footer>
<div class="copy abs">© 2025 Tiny-ThreadDays. All Rights Reserved.</div>

</body>
</html>
```